Business Card Design Project

Mabel's Tonics is a natural skincare business and we need a business card designed. The company focuses on natural products and will be launching with body scrubs and bath fizzies and our mission statement is: To deliver high quality natural beauty products at a good value. It's two cards - one design - the only information changing would be name and email address

Target Market(s)

Females ages 20-50

Industry/Entity Type

Business

Requirements
Must have
• Mabel's Tonics

Wilma Fenwick-Ortiz
T: 800-555-0147
E: Wilma@MabelsTonics.example
W: www.MabelsTonics.example

Teodoro Vasquez
T: 800-555-0147
E: Teodoro@MabelsTonics.example
W: www.MabelsTonics.example
Nice to have
• I'd like to use the colors or text found at www.mabelstonics.example but I'm open to suggestions since design isn't set in stone yet. I would also like to have the words .....a little bit of magic somewhere under the company name in a different type of font. I would like a design that feels clean and maybe a retro feel to it - front and back would be nice but not mandatory

```html
<!DOCTYPE html>
<html lang="en">
<head>
<meta charset="utf-8">
<title>Mabel's Tonics – Business Card</title>
<link rel="stylesheet" href="https://fonts.googleapis.com/css2?family=Open+Sans:wght@400;700&display=swap">
<style>
  :root {
    --plum: #7d1f7c;
    --plum-deep: #560848;
    --magenta: #b04aa8;
    --sky: #2b9fd8;
    --rose: #ec8fa6;
    --lime: #cfe93a;
    --leaf: #a6cf4a;
    --ink: #555555;
    --paper: #ffffff;
  }
  html, body {
    margin: 0;
    padding: 0;
    width: 1200px;
    height: 900px;
    overflow: hidden;
    background: var(--paper);
  }
  .card {
    position: relative;
    width: 1200px;
    height: 900px;
    font-family: "Open Sans", Arial, sans-serif;
  }
  .card-art {
    position: absolute;
    inset: 0;
  }
  .brand-name {
    position: absolute;
    left: 556px;
    top: 150px;
    margin: 0;
    font-weight: 400;
    font-size: 72px;
    line-height: 1;
    color: var(--plum);
    white-space: nowrap;
  }
  .person {
    position: absolute;
    left: 68px;
    top: 386px;
    margin: 0;
    font-weight: 400;
    font-size: 44px;
    line-height: 1.2;
    color: var(--plum);
    white-space: nowrap;
  }
  .person .surname-tail { color: var(--sky); }
  .contact {
    position: absolute;
    left: 68px;
    top: 496px;
    margin: 0;
    padding: 0;
    list-style: none;
    font-size: 40px;
    line-height: 59px;
    color: var(--ink);
    white-space: nowrap;
  }
  .contact .label {
    font-weight: 700;
    color: var(--rose);
  }
  .mission {
    position: absolute;
    left: 60px;
    top: 726px;
    margin: 0;
    font-size: 35px;
    line-height: 1.2;
    color: var(--paper);
    white-space: nowrap;
  }
</style>
</head>
<body>
<main class="card">
  <svg class="card-art" width="1200" height="900" viewBox="0 0 1200 900" aria-hidden="true">
    <defs>
      <linearGradient id="band-fill" x1="0" y1="0" x2="1" y2="0">
        <stop offset="0" stop-color="#560848"/>
        <stop offset="0.55" stop-color="#8a2483"/>
        <stop offset="1" stop-color="#b04aa8"/>
      </linearGradient>
    </defs>
    <circle class="dot-rose" cx="70" cy="282" r="50" fill="var(--rose)" opacity="0.85"/>
    <circle class="brand-dot" cx="510" cy="186" r="30" fill="var(--lime)"/>
    <path class="band" d="M0 712 C 380 700 800 680 1200 636 L1200 836 L0 836 Z" fill="url(#band-fill)"/>
    <rect class="band-base" x="0" y="790" width="1200" height="46" fill="var(--plum-deep)"/>
    <rect class="trim" x="20" y="104" width="1160" height="684" fill="none" stroke="var(--leaf)" stroke-width="2"/>
  </svg>

  <h1 class="brand-name">Mabel's Tonics</h1>

  <h2 class="person">Wilma Fenwick-<span class="surname-tail">Ortiz</span></h2>

  <ul class="contact">
    <li><span class="label">T</span>: 800-555-0147</li>
    <li><span class="label">E</span>: Wilma@MabelsTonics.example</li>
    <li><span class="label">W</span>: www.MabelsTonics.example</li>
  </ul>

  <p class="mission">To deliver high quality natural beauty products at a good value.</p>
</main>
</body>
</html>
```